Brightwave Reach - Business Card

We need a business card for a Social Media Marketing company that specializes in online marketing for small businesses in Canada using common Social Media platforms such as Pixlora, Chatterly, Blinkpost & Quibber.

I have uploaded a copy of our logo which I would like utilized in the business card. We would like the business card to be modern yet classy design.

Our website is www.brightwavereach.ca

Industry/Entity Type

Marketing

Contact Information for Business Card

Email: info@brightwavereach.ca
Website: www.brightwavereach.ca
Telephone: 604-555-0193

Colors

Designer to choose colors to be used in the design.

Requirements
Must have
• Social Media icons on reverse
• Please add some designs with color.

```html
<!DOCTYPE html>
<html lang="en">
<head>
<meta charset="utf-8">
<title>Brightwave Reach – Business Card</title>
<link href="https://fonts.googleapis.com/css2?family=Roboto:wght@400;500;700&family=Roboto+Condensed:wght@700&display=swap" rel="stylesheet">
<style>
  :root {
    --backdrop: #2a2a2a;
    --paper: #eeeeec;
    --slate: #3f4446;
    --slate-deep: #373c3e;
    --ink: #4a4d4f;
    --frame-line: #d9dbdb;
    --white: #ffffff;
    --rule: #8e9294;
  }
  * { box-sizing: border-box; margin: 0; padding: 0; }
  html, body {
    width: 1200px; height: 960px; overflow: hidden;
    background: var(--backdrop);
    font-family: "Roboto", Arial, sans-serif;
  }
  .canvas { position: relative; width: 1200px; height: 960px; }

  .card {
    position: absolute; width: 600px; height: 342px;
    box-shadow: 0 3px 8px rgba(0,0,0,.5);
  }
  .card--front { left: 314px; top: 113px; background: var(--paper); }
  .card--back {
    left: 311px; top: 472px;
    background: radial-gradient(ellipse at 50% 45%, var(--slate) 0%, var(--slate-deep) 100%);
  }

  /* front: brand */
  .brand {
    position: absolute; left: 58px; top: 130px; width: 176px;
    text-align: center; color: var(--ink);
    font-family: "Roboto Condensed", "Arial Narrow", sans-serif; font-weight: 700;
    font-size: 27px; line-height: 29px; letter-spacing: .5px;
  }
  .brand__mark {
    display: block; width: 12px; height: 12px; margin: 8px auto 0;
    background: var(--ink);
  }

  /* front: contact panel */
  .panel {
    position: absolute; left: 293px; top: 15px; width: 290px; height: 313px;
    background: var(--slate); border-radius: 12px;
  }
  .panel__frame {
    position: absolute; inset: 8px;
    border: 2px solid var(--frame-line); border-radius: 3px;
  }
  .panel__frame::after {
    content: ""; position: absolute; inset: 3px;
    border: 1px solid var(--frame-line); opacity: .7;
  }
  .person {
    position: absolute; left: 55px; top: 94px; color: var(--white);
  }
  .person__name { font-weight: 500; font-size: 21px; letter-spacing: .2px; }
  .person__title { font-size: 14px; margin-top: 6px; letter-spacing: .3px; }
  .contacts { list-style: none; margin-top: 20px; font-size: 14px; }
  .contacts li { display: flex; align-items: center; height: 19px; }
  .contacts svg { width: 12px; height: 12px; margin-right: 10px; fill: var(--white); }

  /* back */
  .back-brand {
    position: absolute; left: 0; right: 0; top: 140px;
    text-align: center; color: var(--white);
    font-family: "Roboto Condensed", "Arial Narrow", sans-serif; font-weight: 700;
    font-size: 34px; letter-spacing: 1px;
  }
  .back-brand__mark {
    display: block; width: 14px; height: 14px; margin: 0 auto 14px;
    background: var(--white);
  }
  .socials {
    position: absolute; left: 0; right: 0; top: 287px;
    display: flex; align-items: center; justify-content: center; gap: 12px;
    color: var(--white); font-size: 13px;
  }
  .socials__rule { width: 100px; height: 1px; background: linear-gradient(90deg, transparent, var(--rule)); }
  .socials__rule--right { background: linear-gradient(90deg, var(--rule), transparent); }
  .social { display: flex; align-items: center; gap: 5px; }
  .social::before {
    content: ""; width: 12px; height: 12px; border: 1.5px solid var(--white); border-radius: 50%;
  }
</style>
</head>
<body>
<main class="canvas">
  <section class="card card--front" aria-label="Card front">
    <div class="brand">BRIGHTWAVE<br>REACH<span class="brand__mark"></span></div>
    <div class="panel">
      <div class="panel__frame"></div>
      <div class="person">
        <p class="person__name">ALEX MOREAU</p>
        <p class="person__title">CEO/FOUNDER</p>
        <ul class="contacts">
          <li><svg viewBox="0 0 24 24"><path d="M6.6 10.8a15 15 0 0 0 6.6 6.6l2.2-2.2c.3-.3.7-.4 1-.2 1.1.4 2.3.6 3.6.6.6 0 1 .4 1 1V20c0 .6-.4 1-1 1A17 17 0 0 1 3 4c0-.6.4-1 1-1h3.5c.6 0 1 .4 1 1 0 1.2.2 2.4.6 3.6.1.3 0 .7-.2 1z"/></svg>604-555-0193</li>
          <li><svg viewBox="0 0 24 24"><path d="M2 5h20v14H2zm2 2v.5l8 5 8-5V7l-8 5z"/></svg>info@brightwavereach.ca</li>
          <li><svg viewBox="0 0 24 24"><circle cx="12" cy="12" r="10"/></svg>www.brightwavereach.ca</li>
        </ul>
      </div>
    </div>
  </section>

  <section class="card card--back" aria-label="Card back">
    <div class="back-brand"><span class="back-brand__mark"></span>BRIGHTWAVE REACH</div>
    <div class="socials">
      <span class="socials__rule"></span>
      <span class="social">Chatterly</span>
      <span class="social">Pixlora</span>
      <span class="social">Quibber</span>
      <span class="socials__rule socials__rule--right"></span>
    </div>
  </section>
</main>
</body>
</html>
```